Landscape design build company door flyer

I would like this flyer to convey a high-level of professionalism for a company that is excellent with communication with their clients as well as a company that does incredible installations

Went on vacation/holiday

```html
<!DOCTYPE html>
<html lang="en">
<head>
<meta charset="utf-8">
<title>Cedar Ridge Builders – Outdoor Living Spaces Flyer</title>
<link href="https://fonts.googleapis.com/css2?family=Poppins:wght@400;500;600;700;800&display=swap" rel="stylesheet">
<style>
  :root{
    --navy:#0b2a3e;
    --orange:#f26a0c;
    --amber:#f5a623;
    --paper:#f2f2f2;
    --ink:#1b1b1b;
    --white:#ffffff;
  }
  *{margin:0;padding:0;box-sizing:border-box}
  html,body{width:933px;height:1200px;overflow:hidden;background:var(--paper)}
  body{font-family:"Poppins",sans-serif;color:var(--ink)}
  .flyer{position:relative;width:933px;height:1200px;overflow:hidden;background:var(--paper)}
  .hero-art{position:absolute;left:0;top:0;width:933px;height:564px}
  .brand{position:absolute;left:70px;top:132px;width:230px;display:flex;align-items:center;justify-content:center;gap:8px}
  .brand-mark{width:12px;height:12px;background:var(--orange)}
  .brand-name{font-family:"Poppins",sans-serif;font-weight:600;font-size:21px;color:var(--orange);letter-spacing:.5px;white-space:nowrap}
  .headline{position:absolute;left:42px;top:236px;font-weight:700;font-size:61px;line-height:68px;letter-spacing:-1px;color:var(--white);text-transform:uppercase}
  .headline .accent{color:var(--orange)}
  .section-title{font-weight:800;font-size:27px;color:var(--navy);letter-spacing:-.3px;line-height:1}
  .section-rule{display:block;width:80px;height:3px;border-radius:2px;background:var(--amber);margin-top:8px}
  .about{position:absolute;left:41px;top:589px;width:395px}
  .about p{margin-top:14px;font-size:14.2px;line-height:17.9px;text-align:justify;hyphens:auto}
  .services{position:absolute;left:513px;top:589px}
  .service-list{list-style:none;margin-top:14px}
  .service-list li{display:flex;align-items:center;gap:18px;height:25.3px;font-size:15.5px;font-weight:500;color:var(--navy)}
  .service-list svg{flex:none;width:15px;height:15px}
  .works-rule{position:absolute;left:30px;top:861px;width:871px;height:1.5px;background:linear-gradient(90deg,transparent,var(--amber) 15%,var(--amber) 85%,transparent)}
  .works-title{position:absolute;left:330px;top:842px;width:263px;height:35px;background:var(--orange);color:var(--white);font-weight:800;font-size:21px;display:flex;align-items:center;justify-content:center;letter-spacing:-.3px}
  .works-photo{position:absolute;top:893px;width:252px;height:138px}
  .works-deck{left:45px;background:linear-gradient(180deg,#4f8a3a 0%,#6a9b4a 35%,#8e4e2c 55%,#7a3f22 100%)}
  .works-pool{left:333px;background:linear-gradient(135deg,#5c7a4a 0%,#cfd3d2 30%,#3fb7b3 50%,#dcdfe0 70%,#c8cbcb 100%)}
  .works-fire{left:620px;background:linear-gradient(180deg,#2d3a2f 0%,#4f7fa0 25%,#5d5049 55%,#3a3330 100%)}
  .footer-art{position:absolute;left:0;top:1080px;width:933px;height:120px}
  .call{position:absolute;left:44px;top:1111px;display:flex;align-items:center;gap:15px}
  .call-icon{width:61px;height:61px;background:var(--orange);display:flex;align-items:center;justify-content:center}
  .call-number{font-weight:700;font-size:50px;letter-spacing:-1.5px;color:var(--white);line-height:1}
  .contact{position:absolute;left:610px;top:1105px;list-style:none}
  .contact li{display:flex;align-items:center;gap:22px;height:30px;font-size:16.5px;color:var(--white)}
  .contact svg{flex:none;width:20px;height:20px}
</style>
</head>
<body>
<main class="flyer">
  <svg class="hero-art" viewBox="0 0 933 564" aria-hidden="false">
    <defs>
      <linearGradient id="heroTone" x1="0" y1="0" x2="1" y2="1">
        <stop offset="0" stop-color="#5b7a3c"/>
        <stop offset=".35" stop-color="#6f747a"/>
        <stop offset=".7" stop-color="#4e5459"/>
        <stop offset="1" stop-color="#5a3d2c"/>
      </linearGradient>
    </defs>
    <polygon role="img" aria-label="Aerial photo of a home with a new paver driveway, front steps and landscaped beds" points="429,0 933,0 933,564 300,564 360,191" fill="url(#heroTone)"/>
    <polygon class="hero-panel" points="0,191 434,191 624,564 0,564" fill="#0b2a3e"/>
  </svg>

  <div class="brand">
    <span class="brand-mark"></span>
    <span class="brand-name">CEDAR RIDGE BUILDERS</span>
  </div>

  <h1 class="headline">Let’s create<br>your dream<br><span class="accent">outdoor<br>living space!</span></h1>

  <section class="about">
    <h2 class="section-title">ABOUT US</h2>
    <span class="section-rule"></span>
    <p>Discover the endless possibilities for your outdoor space with The Cedar Ridge Team. Our team of skilled artisans is dedicated to turning your outdoor space into a breathtaking oasis that you’ll love coming home to. Whether it’s a cozy patio for intimate gatherings, a sprawling deck to host memorable parties, or a custom paver driveway that adds instant curb appeal, our high-quality craftsmanship ensures stunning results that exceed your expectations.</p>
  </section>

  <section class="services">
    <h2 class="section-title">OUR SERVICES</h2>
    <span class="section-rule"></span>
    <ul class="service-list">
      <li><svg viewBox="0 0 16 16"><circle cx="8" cy="8" r="8" fill="#f26a0c"/><path d="M4.5 8.3l2.3 2.3 4.7-4.9" fill="none" stroke="#fff" stroke-width="1.8" stroke-linecap="round" stroke-linejoin="round"/></svg>Paver Patios</li>
      <li><svg viewBox="0 0 16 16"><circle cx="8" cy="8" r="8" fill="#f26a0c"/><path d="M4.5 8.3l2.3 2.3 4.7-4.9" fill="none" stroke="#fff" stroke-width="1.8" stroke-linecap="round" stroke-linejoin="round"/></svg>Paver Driveways</li>
      <li><svg viewBox="0 0 16 16"><circle cx="8" cy="8" r="8" fill="#f26a0c"/><path d="M4.5 8.3l2.3 2.3 4.7-4.9" fill="none" stroke="#fff" stroke-width="1.8" stroke-linecap="round" stroke-linejoin="round"/></svg>Retaining Walls</li>
      <li><svg viewBox="0 0 16 16"><circle cx="8" cy="8" r="8" fill="#f26a0c"/><path d="M4.5 8.3l2.3 2.3 4.7-4.9" fill="none" stroke="#fff" stroke-width="1.8" stroke-linecap="round" stroke-linejoin="round"/></svg>Decks &amp; Railings</li>
      <li><svg viewBox="0 0 16 16"><circle cx="8" cy="8" r="8" fill="#f26a0c"/><path d="M4.5 8.3l2.3 2.3 4.7-4.9" fill="none" stroke="#fff" stroke-width="1.8" stroke-linecap="round" stroke-linejoin="round"/></svg>Pools</li>
      <li><svg viewBox="0 0 16 16"><circle cx="8" cy="8" r="8" fill="#f26a0c"/><path d="M4.5 8.3l2.3 2.3 4.7-4.9" fill="none" stroke="#fff" stroke-width="1.8" stroke-linecap="round" stroke-linejoin="round"/></svg>Outdoor Lighting</li>
      <li><svg viewBox="0 0 16 16"><circle cx="8" cy="8" r="8" fill="#f26a0c"/><path d="M4.5 8.3l2.3 2.3 4.7-4.9" fill="none" stroke="#fff" stroke-width="1.8" stroke-linecap="round" stroke-linejoin="round"/></svg>Firepits &amp; Fireplaces</li>
    </ul>
  </section>

  <div class="works-rule"></div>
  <h2 class="works-title">OUR WORKS</h2>
  <div class="works-photo works-deck" role="img" aria-label="Photo of a stained wood deck with pergola and patio chairs"></div>
  <div class="works-photo works-pool" role="img" aria-label="Aerial photo of a plunge pool framed by composite decking and pale pavers"></div>
  <div class="works-photo works-fire" role="img" aria-label="Photo of a paver patio with lit seat walls, a fire pit and a pool beyond"></div>

  <svg class="footer-art" viewBox="0 0 933 120" aria-hidden="true">
    <rect x="0" y="10" width="933" height="110" fill="#0b2a3e"/>
    <polygon points="569,0 933,0 933,120 517,120" fill="#f26a0c"/>
  </svg>

  <div class="call">
    <span class="call-icon">
      <svg width="34" height="34" viewBox="0 0 24 24"><path d="M6.6 2.5l2.6 3.9c.4.6.3 1.3-.2 1.8L7.5 9.6c1.1 2.6 3.3 4.8 5.9 5.9l1.4-1.5c.5-.5 1.2-.6 1.8-.2l3.9 2.6c.6.4.8 1.2.4 1.8l-1.3 2.1c-.6 1-1.8 1.5-2.9 1.2C10.6 19.8 4.2 13.4 2.5 7.3c-.3-1.1.2-2.3 1.2-2.9l2.1-1.3c.3-.2.6-.3.8-.6z" fill="#fff"/></svg>
    </span>
    <span class="call-number">206-555-0148</span>
  </div>

  <ul class="contact">
    <li><svg viewBox="0 0 24 24"><rect x="2" y="5" width="20" height="14" fill="#fff"/><path d="M2.5 5.5L12 13l9.5-7.5" fill="none" stroke="#f26a0c" stroke-width="1.8"/></svg>info@cedarridgebuilders.com</li>
    <li><svg viewBox="0 0 24 24" fill="none" stroke="#fff" stroke-width="1.5"><circle cx="12" cy="12" r="9"/><ellipse cx="12" cy="12" rx="4" ry="9"/><path d="M3 12h18M4.5 7.5h15M4.5 16.5h15"/></svg>www.cedarridgebuilders.com</li>
  </ul>
</main>
</body>
</html>
```